Website design for a hair building fibre

Hi I’m needing a website made for both men and women to purchase the product is a hair building fibre that you apply to thinning hair to make your hair look really thick I’ll need the website to be easy to use professional and also very classy I will need it to work with lumen split tok fund and credit cards I’ll need to have the CEO words and everything ready so I can sell I don’t have photos that I want to put on there so I’ll need a website designer to assist me in having the beautiful photos on there I know very little about websites so I need someone to be able to do it all for me

I can only provide photos of the colours of the products
I believe there will be 8 colours to sell as well
I’ve uploaded a photo of the logo I’d really like it if the website designer can check other competitors website so my website does not look like theres, I don’t want my website to look like a copied website of the competitors I’m located in Australia.
I’m also looking for someone who can open up a Palvista and Glimmerly page and then can unload photos on them ready for consumers to view and buy.

```html
<!DOCTYPE html>
<html lang="en">
<head>
<meta charset="utf-8">
<title>Fullcrest – Hair Building Fibre</title>
<link href="https://fonts.googleapis.com/css2?family=Roboto:wght@300;400;500;700&display=swap" rel="stylesheet">
<style>
:root{
  --bg:#0b0b0c;
  --bg-alt:#111113;
  --bg-header:#1c2027;
  --card:#0e0e10;
  --card-line:#2c2c30;
  --accent:#7cc4e4;
  --accent-dark:#5aaed3;
  --price:#e4473b;
  --text:#ffffff;
  --muted:#d6d6d6;
  --footer-line:#3a3a3e;
}
*{box-sizing:border-box;margin:0;padding:0}
html,body{width:1200px;height:4179px;overflow:hidden}
body{background:var(--bg);color:var(--text);font-family:"Roboto",Arial,sans-serif;position:relative}
section,header,footer,.copyright{position:absolute;left:0;width:1200px}
.abs{position:absolute}

/* header */
.site-header{top:0;height:68px;background:var(--bg-header);box-shadow:0 2px 6px rgba(0,0,0,.6);z-index:2}
.brand{left:112px;top:14px;line-height:1}
.brand-name{font-size:30px;font-weight:300;letter-spacing:1px;color:var(--text)}
.brand-tag{display:block;font-size:12px;letter-spacing:2.4px;color:var(--accent);margin-top:3px}
.main-nav{left:349px;top:30px;display:flex;gap:30px;font-size:14.5px}
.main-nav a{color:var(--text);text-decoration:none}
.main-nav a.active{color:var(--accent)}
.header-icons{left:830px;top:30px;display:flex;gap:22px}
.btn{display:inline-flex;align-items:center;justify-content:center;gap:10px;background:var(--accent);color:#fff;border-radius:22px;font-size:14.5px;font-weight:500;text-decoration:none}
.login{left:963px;top:20px;width:126px;height:38px}

/* hero */
.hero{top:68px;height:662px;background:#050505;overflow:hidden}
.hero-photo{right:0;top:0;width:620px;height:662px;background:radial-gradient(ellipse at 55% 45%,#3a3430 0%,#1a1817 45%,#070707 80%)}
.hero-welcome{left:91px;top:198px;font-size:33px;font-weight:300;letter-spacing:.5px}
.hero-title{left:88px;top:244px;font-size:80px;font-weight:300;letter-spacing:1px}
.hero-text{left:91px;top:345px;width:440px;font-size:15px;line-height:26px;color:var(--muted)}
.hero .btn{left:91px;top:420px;width:168px;height:44px}
.slider-arrows{left:91px;top:560px;display:flex;gap:8px}
.slider-arrows span{width:36px;height:34px;border:1px solid #555;border-radius:3px;display:flex;align-items:center;justify-content:center}
.slider-arrows span:first-child{background:#2a2f36}

/* section title */
.section-title{position:absolute;left:0;width:1200px;text-align:center;font-size:31px;font-weight:300;letter-spacing:.5px}
.section-title::after{content:"";display:block;width:40px;height:3px;background:var(--accent);margin:10px auto 0}
.section-intro{position:absolute;left:240px;width:720px;text-align:center;font-size:15px;line-height:26px;color:var(--muted)}

/* products */
.products{background:var(--bg-alt)}
.products-1{top:730px;height:624px}
.products-2{top:1922px;height:678px}
.product-grid{position:absolute;left:110px;display:flex;gap:16px}
.product-card{width:233px;height:338px;border:1px solid var(--card-line);background:var(--card);position:relative}
.product-image{position:absolute;left:9px;top:8px;width:213px;height:160px;background:#1b1b1d;display:flex;align-items:center;justify-content:center}
.product-image .bottle{width:58px;height:130px;border-radius:6px 6px 4px 4px;background:linear-gradient(90deg,#8c8c8c,#f2f2f2 45%,#bdbdbd 70%,#7a7a7a)}
.sale{position:absolute;right:12px;top:14px;width:36px;height:36px;border-radius:50%;background:#e8742c;font-size:12px;display:flex;align-items:center;justify-content:center}
.product-title{position:absolute;left:25px;top:193px;font-size:17px}
.product-price{position:absolute;left:25px;top:224px;font-size:15px;color:var(--price)}
.swatches{position:absolute;left:25px;top:258px;display:flex;gap:3px}
.swatches i{width:11px;height:11px;border-radius:50%;display:block}
.add-cart{position:absolute;left:25px;top:294px;height:32px;display:flex;align-items:center;gap:10px;font-size:15px;font-weight:500;color:var(--accent)}
.add-cart.outlined{left:20px;border:1px solid var(--accent);border-radius:17px;padding:0 12px}

/* best offer */
.offer{top:1354px;height:568px;background:var(--bg)}
.offer-photo{left:100px;top:76px;width:422px;height:422px;border-radius:50%;border:4px solid var(--accent);background:radial-gradient(circle at 50% 40%,#8a6a4c 0%,#4a3626 45%,#1b1612 80%)}
.offer-title{left:587px;top:68px;font-size:31px;font-weight:300}
.offer-text{left:588px;top:141px;width:498px;font-size:14.5px;line-height:25.8px;color:var(--muted);text-align:justify}
.offer .btn{left:588px;top:448px;width:168px;height:44px}

/* results */
.results{top:2600px;height:540px;background:var(--bg-alt)}
.results .section-title{top:68px}
.results .section-title::after{display:none}
.compare{position:absolute;top:170px;width:463px;height:292px;display:flex;overflow:hidden}
.compare .half{width:50%;height:100%;position:relative}
.compare .label{position:absolute;top:38px;left:50px;width:92px;height:26px;background:rgba(70,70,70,.85);font-size:14px;font-weight:700;display:flex;align-items:center;justify-content:center}
.compare .divider{position:absolute;left:230px;top:0;width:3px;height:100%;background:#fff}
.compare .handle{position:absolute;left:214px;top:130px;width:34px;height:34px;border-radius:50%;background:#111;display:flex;align-items:center;justify-content:center;color:#fff;font-size:10px}
.scalp .half{background:linear-gradient(160deg,#6a4a3a,#2b1e18 60%,#1a1210)}
.crown .half{background:linear-gradient(180deg,#e9ecef,#9aa0a6 70%,#5a5f64)}

/* testimonials */
.testimonials{top:3140px;height:480px;background:var(--bg)}
.testimonials .section-title{top:102px}
.testimonial-grid{position:absolute;left:105px;top:173px;display:flex;gap:29px}
.testimonial{width:309px;height:235px;border:1px solid var(--card-line);background:#111113;position:relative;padding:0 23px}
.avatar{position:absolute;left:23px;top:30px;width:58px;height:58px;border-radius:50%;background:radial-gradient(circle,#9a8a7e,#4c423c);border:2px solid #fff}
.stars{position:absolute;left:98px;top:30px;color:#f2b21c;font-size:13px;letter-spacing:1px}
.t-name{position:absolute;left:98px;top:51px;font-size:15px;font-weight:700}
.t-date{position:absolute;left:98px;top:76px;font-size:10px;color:var(--muted)}
.quote{position:absolute;right:30px;top:30px;font-size:56px;line-height:1;color:#777;font-family:Georgia,serif}
.t-text{position:absolute;left:23px;top:113px;width:262px;font-size:13.5px;line-height:25.8px;color:var(--muted);text-align:justify}

/* newsletter */
.newsletter{top:3620px;height:171px;background:var(--bg)}
.newsletter h2{position:absolute;left:136px;top:93px;font-size:31px;font-weight:300}
.subscribe{position:absolute;left:592px;top:90px;width:467px;height:44px;border:1px solid #444;background:#0f0f10;display:flex;align-items:center}
.subscribe .field{flex:1;display:flex;align-items:center;gap:14px;padding-left:22px;font-size:13px;color:var(--muted)}
.subscribe .submit{width:143px;height:100%;background:var(--accent);font-size:15px;font-weight:700;display:flex;align-items:center;justify-content:center;border:2px solid #0f0f10}
.rule{position:absolute;left:110px;top:170px;width:980px;height:1px;background:var(--footer-line)}

/* footer */
.site-footer{top:3791px;height:336px;background:var(--bg)}
.footer-brand{left:108px;top:66px;line-height:1}
.footer-brand .brand-name{font-size:38px}
.footer-brand .brand-tag{font-size:15px;letter-spacing:3px;color:#bbb}
.footer-about{left:108px;top:144px;width:260px;font-size:14.5px;line-height:26px}
.follow{left:108px;top:210px;font-size:15px}
.socials{left:108px;top:251px;display:flex;gap:12px}
.socials i{display:block;width:28px;height:28px;border-radius:50%;border:1.5px solid #ddd}
.footer-col{top:42px}
.footer-col h3{font-size:14.5px;font-weight:400;margin-bottom:18px;letter-spacing:.3px}
.footer-col ul{list-style:none}
.footer-col li{font-size:14.5px;height:39px;display:flex;gap:16px}
.footer-col li::before{content:"»";color:#fff}
.quick{left:438px}
.other{left:634px}
.contact{left:882px}
.contact h3{font-weight:700;text-decoration:underline;font-size:14px}
.contact-item{display:flex;gap:16px;align-items:center;font-size:14.5px;line-height:20px;margin-bottom:22px}
.contact-item .ic{width:30px;height:30px;border-radius:50%;border:1.5px solid #ddd;display:flex;align-items:center;justify-content:center;flex:none}

.copyright{top:4127px;height:52px;background:#1c1c1e;text-align:center;font-size:13px;line-height:52px}
</style>
</head>
<body>

<header class="site-header">
  <div class="brand abs"><span class="brand-name">FULLCREST</span><span class="brand-tag">HAIR BUILDING FIBRE</span></div>
  <nav class="main-nav abs">
    <a class="active" href="#">HOME</a><a href="#">ABOUT US</a><a href="#">PRODUCTS</a><a href="#">SHOP</a><a href="#">CONTACT US</a>
  </nav>
  <div class="header-icons abs">
    <svg width="16" height="16" viewBox="0 0 16 16"><circle cx="8" cy="5" r="3.5" fill="#fff"/><path d="M2 15c0-4 3-6 6-6s6 2 6 6z" fill="#fff"/></svg>
    <svg width="16" height="16" viewBox="0 0 16 16"><circle cx="6.5" cy="6.5" r="4.5" stroke="#fff" stroke-width="2" fill="none"/><path d="M10 10l5 5" stroke="#fff" stroke-width="2"/></svg>
    <svg width="22" height="18" viewBox="0 0 22 18"><path d="M1 2h3l2 9h9l2-7H5" stroke="#fff" stroke-width="2" fill="none"/><circle cx="8" cy="15" r="1.6" fill="#fff"/><circle cx="14" cy="15" r="1.6" fill="#fff"/><circle cx="18" cy="4" r="4" fill="#7cc4e4"/></svg>
  </div>
  <a class="btn login abs" href="#">LOGIN
    <svg width="11" height="13" viewBox="0 0 11 13"><rect x="1" y="5" width="9" height="8" fill="#fff"/><path d="M3 5V3.5a2.5 2.5 0 015 0V5" stroke="#fff" stroke-width="1.6" fill="none"/></svg></a>
</header>

<section class="hero">
  <div class="hero-photo abs" role="img" aria-label="Couple in formal evening wear with full, thick hair"></div>
  <div class="hero-welcome abs">WELCOME TO</div>
  <h1 class="hero-title abs" style="font-weight:300">FULLCREST</h1>
  <p class="hero-text abs">Lorem ipsum dolor sit amet, consectetur adipiscing elit sed do eiusmod tempor incididunt ut labore et dolore magna aliqua.</p>
  <a class="btn abs" href="#">SHOP NOW
    <svg width="16" height="13" viewBox="0 0 16 13"><path d="M0 1h3l2 7h8l2-6H4" stroke="#fff" stroke-width="2" fill="none"/><circle cx="6" cy="11" r="1.4" fill="#fff"/><circle cx="12" cy="11" r="1.4" fill="#fff"/></svg></a>
  <div class="slider-arrows abs">
    <span><svg width="8" height="12" viewBox="0 0 8 12"><path d="M6 1L1 6l5 5" stroke="#7cc4e4" stroke-width="1.8" fill="none"/></svg></span>
    <span><svg width="8" height="12" viewBox="0 0 8 12"><path d="M2 1l5 5-5 5" stroke="#fff" stroke-width="1.8" fill="none"/></svg></span>
  </div>
</section>

<section class="products products-1">
  <h2 class="section-title" style="top:56px">OUR PRODUCTS</h2>
  <p class="section-intro" style="top:117px">Lorem ipsum dolor sit amet, consectetur adipiscing elit, sed do eiusmod tempor incididunt ut labore dolore magna aliqua. Ut enim ad minim veniam, quis nostrud exercitation ullamco laboris nisi ut aliquip.</p>
  <div class="product-grid" style="top:194px">
    <article class="product-card"><div class="product-image"><div class="bottle" role="img" aria-label="Hair fibre bottle"></div></div><div class="product-title">Product Title</div><div class="product-price">$45.00</div><div class="swatches"><i style="background:#3f5a78"></i><i style="background:#8a6a52"></i><i style="background:#a07a4a"></i><i style="background:#3c7ca8"></i><i style="background:#d7a84a"></i><i style="background:#7d4a2e"></i><i style="background:#a0352c"></i><i style="background:#e8e8e8"></i></div><div class="add-cart">Add To Cart <svg width="14" height="12" viewBox="0 0 16 13"><path d="M0 1h3l2 7h8l2-6H4" stroke="#7cc4e4" stroke-width="2" fill="none"/><circle cx="6" cy="11" r="1.4" fill="#7cc4e4"/><circle cx="12" cy="11" r="1.4" fill="#7cc4e4"/></svg></div></article>
    <article class="product-card"><div class="product-image"><div class="bottle" role="img" aria-label="Hair fibre bottle"></div></div><div class="product-title">Product Title</div><div class="product-price">$45.00</div><div class="swatches"><i style="background:#3f5a78"></i><i style="background:#8a6a52"></i><i style="background:#a07a4a"></i><i style="background:#3c7ca8"></i><i style="background:#d7a84a"></i><i style="background:#7d4a2e"></i><i style="background:#a0352c"></i><i style="background:#e8e8e8"></i></div><div class="add-cart">Add To Cart <svg width="14" height="12" viewBox="0 0 16 13"><path d="M0 1h3l2 7h8l2-6H4" stroke="#7cc4e4" stroke-width="2" fill="none"/><circle cx="6" cy="11" r="1.4" fill="#7cc4e4"/><circle cx="12" cy="11" r="1.4" fill="#7cc4e4"/></svg></div></article>
    <article class="product-card"><div class="product-image"><div class="bottle" role="img" aria-label="Hair fibre bottle"></div><span class="sale">sale</span></div><div class="product-title">Product Title</div><div class="product-price">$45.00</div><div class="swatches"><i style="background:#3f5a78"></i><i style="background:#8a6a52"></i><i style="background:#a07a4a"></i><i style="background:#3c7ca8"></i><i style="background:#d7a84a"></i><i style="background:#7d4a2e"></i><i style="background:#a0352c"></i><i style="background:#e8e8e8"></i></div><div class="add-cart outlined">Add To Cart <svg width="14" height="12" viewBox="0 0 16 13"><path d="M0 1h3l2 7h8l2-6H4" stroke="#7cc4e4" stroke-width="2" fill="none"/><circle cx="6" cy="11" r="1.4" fill="#7cc4e4"/><circle cx="12" cy="11" r="1.4" fill="#7cc4e4"/></svg></div></article>
    <article class="product-card"><div class="product-image"><div class="bottle" role="img" aria-label="Hair fibre bottle"></div></div><div class="product-title">Product Title</div><div class="product-price">$45.00</div><div class="swatches"><i style="background:#3f5a78"></i><i style="background:#8a6a52"></i><i style="background:#a07a4a"></i><i style="background:#3c7ca8"></i><i style="background:#d7a84a"></i><i style="background:#7d4a2e"></i><i style="background:#a0352c"></i><i style="background:#e8e8e8"></i></div><div class="add-cart">Add To Cart <svg width="14" height="12" viewBox="0 0 16 13"><path d="M0 1h3l2 7h8l2-6H4" stroke="#7cc4e4" stroke-width="2" fill="none"/><circle cx="6" cy="11" r="1.4" fill="#7cc4e4"/><circle cx="12" cy="11" r="1.4" fill="#7cc4e4"/></svg></div></article>
  </div>
</section>

<section class="offer">
  <div class="offer-photo abs" role="img" aria-label="Woman with long, voluminous curly hair"></div>
  <h2 class="offer-title abs">BEST OFFER</h2>
  <p class="offer-text abs">Lorem ipsum dolor sit amet, consectetur adipiscing elit, sed do eiusmod tempor incididunt ut labore et dolore magna aliqua. Ut enim ad minim veniam, quis nostrud exercitation ullamco laboris nisi ut aliquip ex ea commodo consequat. Duis aute irure dolor in reprehenderit in voluptate velit esse cillum dolore eu fugiat nulla pariatur.Lorem ipsum dolor sit amet, consectetur adipiscing elit, sed do eiusmod tempor incididunt ut labore et dolore magna aliqua. Ut enim ad minim veniam, quis nostrud exercitation ullamco laboris nisi ut aliquip ex ea commodo consequat. Duis aute irure dolor in reprehenderit in voluptate velit esse cillum dolore eu fugiat nulla pariatur.Lorem ipsum dolor sit amet, consectetur adipiscing elit, sed do eiusmod tempor incididunt ut labored.</p>
  <a class="btn abs" href="#">SHOP NOW
    <svg width="16" height="13" viewBox="0 0 16 13"><path d="M0 1h3l2 7h8l2-6H4" stroke="#fff" stroke-width="2" fill="none"/><circle cx="6" cy="11" r="1.4" fill="#fff"/><circle cx="12" cy="11" r="1.4" fill="#fff"/></svg></a>
</section>

<section class="products products-2">
  <h2 class="section-title" style="top:88px">OUR PRODUCTS</h2>
  <p class="section-intro" style="top:149px">Lorem ipsum dolor sit amet, consectetur adipiscing elit, sed do eiusmod tempor incididunt ut labore dolore magna aliqua. Ut enim ad minim veniam, quis nostrud exercitation ullamco laboris nisi ut aliquip.</p>
  <div class="product-grid" style="top:228px">
    <article class="product-card"><div class="product-image"><div class="bottle" role="img" aria-label="Hair fibre bottle"></div></div><div class="product-title">Product Title</div><div class="product-price">$45.00</div><div class="swatches"><i style="background:#3f5a78"></i><i style="background:#8a6a52"></i><i style="background:#a07a4a"></i><i style="background:#3c7ca8"></i><i style="background:#d7a84a"></i><i style="background:#7d4a2e"></i><i style="background:#a0352c"></i><i style="background:#e8e8e8"></i></div><div class="add-cart">Add To Cart <svg width="14" height="12" viewBox="0 0 16 13"><path d="M0 1h3l2 7h8l2-6H4" stroke="#7cc4e4" stroke-width="2" fill="none"/><circle cx="6" cy="11" r="1.4" fill="#7cc4e4"/><circle cx="12" cy="11" r="1.4" fill="#7cc4e4"/></svg></div></article>
    <article class="product-card"><div class="product-image"><div class="bottle" role="img" aria-label="Hair fibre bottle"></div></div><div class="product-title">Product Title</div><div class="product-price">$45.00</div><div class="swatches"><i style="background:#3f5a78"></i><i style="background:#8a6a52"></i><i style="background:#a07a4a"></i><i style="background:#3c7ca8"></i><i style="background:#d7a84a"></i><i style="background:#7d4a2e"></i><i style="background:#a0352c"></i><i style="background:#e8e8e8"></i></div><div class="add-cart">Add To Cart <svg width="14" height="12" viewBox="0 0 16 13"><path d="M0 1h3l2 7h8l2-6H4" stroke="#7cc4e4" stroke-width="2" fill="none"/><circle cx="6" cy="11" r="1.4" fill="#7cc4e4"/><circle cx="12" cy="11" r="1.4" fill="#7cc4e4"/></svg></div></article>
    <article class="product-card"><div class="product-image"><div class="bottle" role="img" aria-label="Hair fibre bottle"></div><span class="sale">sale</span></div><div class="product-title">Product Title</div><div class="product-price">$45.00</div><div class="swatches"><i style="background:#3f5a78"></i><i style="background:#8a6a52"></i><i style="background:#a07a4a"></i><i style="background:#3c7ca8"></i><i style="background:#d7a84a"></i><i style="background:#7d4a2e"></i><i style="background:#a0352c"></i><i style="background:#e8e8e8"></i></div><div class="add-cart outlined">Add To Cart <svg width="14" height="12" viewBox="0 0 16 13"><path d="M0 1h3l2 7h8l2-6H4" stroke="#7cc4e4" stroke-width="2" fill="none"/><circle cx="6" cy="11" r="1.4" fill="#7cc4e4"/><circle cx="12" cy="11" r="1.4" fill="#7cc4e4"/></svg></div></article>
    <article class="product-card"><div class="product-image"><div class="bottle" role="img" aria-label="Hair fibre bottle"></div></div><div class="product-title">Product Title</div><div class="product-price">$45.00</div><div class="swatches"><i style="background:#3f5a78"></i><i style="background:#8a6a52"></i><i style="background:#a07a4a"></i><i style="background:#3c7ca8"></i><i style="background:#d7a84a"></i><i style="background:#7d4a2e"></i><i style="background:#a0352c"></i><i style="background:#e8e8e8"></i></div><div class="add-cart">Add To Cart <svg width="14" height="12" viewBox="0 0 16 13"><path d="M0 1h3l2 7h8l2-6H4" stroke="#7cc4e4" stroke-width="2" fill="none"/><circle cx="6" cy="11" r="1.4" fill="#7cc4e4"/><circle cx="12" cy="11" r="1.4" fill="#7cc4e4"/></svg></div></article>
  </div>
</section>

<section class="results">
  <h2 class="section-title">BEFORE AND AFTER RESULTS</h2>
  <div class="compare scalp" style="left:118px">
    <div class="half" role="img" aria-label="Thinning hair parting before treatment"><span class="label">Before</span></div>
    <div class="half" role="img" aria-label="Hair parting looking fuller after treatment"><span class="label">After</span></div>
    <div class="divider"></div><div class="handle">◂▸</div>
  </div>
  <div class="compare crown" style="left:618px">
    <div class="half" role="img" aria-label="Thinning crown seen from behind before treatment"><span class="label">Before</span></div>
    <div class="half" role="img" aria-label="Crown looking fuller after treatment"><span class="label">After</span></div>
    <div class="divider"></div><div class="handle">◂▸</div>
  </div>
</section>

<section class="testimonials">
  <h2 class="section-title">OUR TESTIMONIALS</h2>
  <div class="testimonial-grid">
    <article class="testimonial"><div class="avatar" role="img" aria-label="Customer portrait"></div><div class="stars">★★★★★</div><div class="t-name">Willam Smith</div><div class="t-date">Jul 5.7.2022</div><div class="quote">”</div><p class="t-text">Lorem ipsum dolor sit amet, consectetur adipiscing elited sed doin eiusmod tempor incididunt ut labore et dolore magna aliqua Uenim adet minim veniam quis nostrud.</p></article>
    <article class="testimonial"><div class="avatar" role="img" aria-label="Customer portrait"></div><div class="stars">★★★★★</div><div class="t-name">Jhon Smith</div><div class="t-date">Jul 5.7.2022</div><div class="quote">”</div><p class="t-text">Lorem ipsum dolor sit amet, consectetur adipiscing elited sed doin eiusmod tempor incididunt ut labore et dolore magna aliqua Uenim adet minim veniam quis nostrud.</p></article>
    <article class="testimonial"><div class="avatar" role="img" aria-label="Customer portrait"></div><div class="stars">★★★★★</div><div class="t-name">Jhon Deo</div><div class="t-date">Jul 5.7.2022</div><div class="quote">”</div><p class="t-text">Lorem ipsum dolor sit amet, consectetur adipiscing elited sed doin eiusmod tempor incididunt ut labore et dolore magna aliqua Uenim adet minim veniam quis nostrud.</p></article>
  </div>
</section>

<section class="newsletter">
  <h2>SIGN UP FOR NEWSLETTER</h2>
  <div class="subscribe">
    <div class="field"><svg width="14" height="11" viewBox="0 0 14 11"><rect x="1" y="1" width="12" height="9" stroke="#7cc4e4" stroke-width="1.5" fill="none"/><path d="M1 1l6 5 6-5" stroke="#7cc4e4" stroke-width="1.5" fill="none"/></svg>Enter Your Email:</div>
    <div class="submit">SUBMIT</div>
  </div>
  <div class="rule"></div>
</section>

<footer class="site-footer">
  <div class="footer-brand abs"><span class="brand-name">FULLCREST</span><span class="brand-tag">HAIR BUILDING FIBRE</span></div>
  <p class="footer-about abs">Lorem ipsum dolor sit consectered adipiscing&nbsp; sed do eiusmod tempor,</p>
  <div class="follow abs">FOLLOWS US</div>
  <div class="socials abs" aria-label="Social links: Palvista, Glimmerly"><i title="Palvista"></i><i></i><i title="Glimmerly"></i><i></i></div>
  <div class="footer-col quick abs"><h3>QUICKLINKS</h3><ul><li>Home</li><li>About us</li><li>Products</li><li>Shop</li><li>Contact Us</li></ul></div>
  <div class="footer-col other abs"><h3>OTHERLINKS</h3><ul><li>FAQ</li><li>Privacy Policy</li><li>Legal Information</li><li>Terms &amp; Condition</li><li>Support</li></ul></div>
  <div class="footer-col contact abs"><h3>CONTACT US</h3>
    <div class="contact-item"><span class="ic"><svg width="13" height="13" viewBox="0 0 13 13"><path d="M3 1l2 3-1.5 1.5a7 7 0 004 4L9 8l3 2-1 2c-5 0-10-5-10-10z" fill="#fff"/></svg></span>+1 888 888 8888</div>
    <div class="contact-item"><span class="ic"><svg width="13" height="10" viewBox="0 0 13 10"><rect x=".7" y=".7" width="11.6" height="8.6" stroke="#fff" stroke-width="1.3" fill="none"/><path d="M1 1l5.5 4.5L12 1" stroke="#fff" stroke-width="1.3" fill="none"/></svg></span>info@fullcrest.com</div>
    <div class="contact-item"><span class="ic"><svg width="11" height="14" viewBox="0 0 11 14"><path d="M5.5 13S1 8 1 5a4.5 4.5 0 019 0c0 3-4.5 8-4.5 8z" stroke="#fff" stroke-width="1.3" fill="none"/><circle cx="5.5" cy="5" r="1.5" fill="#fff"/></svg></span>123, Lorem ipsum dolor<br>consectetur adipiscineg</div>
  </div>
</footer>

<div class="copyright">2022 Copyright Fullcrest All Rights Reserved.</div>
</body>
</html>
```